Flyer for the Radiant Harvest Worship Day

I am looking to create a flyer for a one day prayer retreat our church is organizing.
This flyer will be posted on social media, websites and will also be printed so it can be mailed to people.
I am looking for something professional, with good use of our logo and band colors (logo colors).
I am counting on the designer's skill, creativity, art and knowledge of media communication to produce a flyer that will effectively and quickly convey the message we are trying to spread.
CONTENT OF THE FLYER:
Event title: Radiant Harvest Worship Day
Date: Tuesday July 2nd, 2019
Time: 11:00AM - 7:00PM
Belmora Hotel, 4875 Wexley Avenue, Portland, Maine 04102 (Room: Juniper)
Event Key words to highlight what the event is about: Prayer, Sharing the Word, Panel discussion, prophecy, Impartation.
Key phrases:
A one day prayer retreat.
Jesus Chris is Lord
Contact info:
www.tolvex.org
Phone: 207 555 3184
Email: contact@brookhavenfold.org

```html
<!DOCTYPE html>
<html lang="en">
<head>
<meta charset="utf-8">
<title>Radiant Harvest Worship Day</title>
<link href="https://fonts.googleapis.com/css2?family=Oswald:wght@500;600&family=Arimo:wght@400;700&display=swap" rel="stylesheet">
<style>
  :root {
    --navy: #0d3a5f;
    --orange: #f39219;
    --white: #ffffff;
    --rule: #8a8a8a;
    --photo-light: #e9e9e9;
    --photo-mid: #a9a9a9;
    --photo-dark: #4a4a4a;
  }
  html, body { margin: 0; padding: 0; overflow: hidden; }
  body { width: 866px; height: 1200px; background: var(--white); font-family: "Arimo", Arial, sans-serif; }
  .flyer { position: relative; width: 866px; height: 1200px; overflow: hidden; }
  .frame { position: absolute; left: 41px; top: 48px; width: 781px; height: 1104px; border: 1px solid var(--rule); box-sizing: border-box; }
  .top-band { position: absolute; left: 41px; top: 48px; width: 781px; height: 34px; background: var(--navy); }
  .hero-photo { position: absolute; left: 41px; top: 82px; width: 781px; height: 540px;
    background: linear-gradient(110deg, var(--photo-dark) 0%, var(--photo-mid) 30%, var(--photo-light) 60%, #f2f2f2 100%); }
  .brand-box { position: absolute; left: 548px; top: 82px; width: 232px; height: 196px; background: var(--navy);
    display: flex; align-items: center; justify-content: center; gap: 10px; }
  .brand-dot { width: 18px; height: 18px; border-radius: 50%; background: var(--orange); }
  .brand-name { font-family: "Oswald", sans-serif; font-weight: 500; font-size: 46px; color: var(--white); letter-spacing: 1px; }
  .event-title { position: absolute; right: 86px; top: 440px; text-align: right; font-family: "Oswald", sans-serif; font-weight: 600; line-height: 1; }
  .event-title .line-accent { display: block; color: var(--orange); font-size: 46px; }
  .event-title .line-main { display: block; color: var(--navy); font-size: 68px; margin-top: 6px; }
  .divider-band { position: absolute; left: 41px; top: 622px; width: 781px; height: 14px; background: var(--navy); }
  .tagline-band { position: absolute; left: 41px; top: 636px; width: 781px; height: 116px; background: var(--orange); text-align: center; }
  .tagline { margin: 6px 0 0; font-family: "Oswald", sans-serif; font-weight: 600; font-size: 62px; line-height: 72px; color: var(--white); }
  .confession { margin: 0; font-family: "Arimo", sans-serif; font-weight: 700; font-size: 25px; color: var(--navy); line-height: 30px; }
  .info-panel { position: absolute; left: 41px; top: 752px; width: 781px; height: 400px; background: var(--navy); color: var(--white); }
  .keywords { position: absolute; top: 22px; left: 0; width: 100%; text-align: center; font-weight: 700; font-size: 29px; line-height: 40px; margin: 0; }
  .details { position: absolute; top: 118px; left: 0; width: 100%; font-size: 23px; line-height: 36px; }
  .detail { position: absolute; top: 0; display: flex; gap: 8px; }
  .detail svg { flex: none; margin-top: 2px; }
  .detail-date { left: 64px; }
  .detail-time { left: 272px; }
  .detail-venue { left: 458px; }
  .detail-venue p { margin: 0; }
  .detail p { margin: 0; }
  .vrule { position: absolute; top: 0; width: 1px; height: 106px; background: var(--orange); }
  .vrule-1 { left: 254px; }
  .vrule-2 { left: 440px; }
  .footer-rule { position: absolute; left: 34px; top: 284px; width: 713px; height: 1px; background: #6f8aa3; }
  .footer-brand { position: absolute; left: 72px; top: 310px; display: flex; align-items: center; gap: 10px; }
  .footer-brand .brand-name { font-size: 48px; }
  .contacts { position: absolute; left: 274px; top: 298px; font-size: 29px; line-height: 38px; }
  .contact { display: flex; align-items: center; gap: 12px; }
</style>
</head>
<body>
<div class="flyer">
  <div class="frame"></div>
  <div class="top-band"></div>
  <div class="hero-photo" role="img" aria-label="Black and white photo of clasped praying hands holding a cross on a cord"></div>
  <div class="brand-box">
    <span class="brand-dot"></span>
    <span class="brand-name">TOLVEX</span>
  </div>
  <h1 class="event-title" style="margin:0">
    <span class="line-accent">RADIANT HARVEST</span>
    <span class="line-main">WORSHIP DAY</span>
  </h1>
  <div class="divider-band"></div>
  <div class="tagline-band">
    <p class="tagline">A ONE DAY PRAYER RETREAT.</p>
    <p class="confession">JESUS CHRIS IS LORD</p>
  </div>
  <div class="info-panel">
    <p class="keywords">Prayer | Sharing the Word<br>Panel discussion | Prophecy | Impartation.</p>
    <div class="details">
      <div class="detail detail-date">
        <svg width="30" height="30" viewBox="0 0 30 30"><circle cx="15" cy="15" r="15" fill="#f39219"/><rect x="8" y="9" width="14" height="13" rx="1.5" fill="none" stroke="#fff" stroke-width="1.6"/><line x1="8" y1="13" x2="22" y2="13" stroke="#fff" stroke-width="1.6"/><line x1="11" y1="7" x2="11" y2="10" stroke="#fff" stroke-width="1.6"/><line x1="19" y1="7" x2="19" y2="10" stroke="#fff" stroke-width="1.6"/></svg>
        <p>Tuesday<br>July 2nd, 2019</p>
      </div>
      <div class="vrule vrule-1"></div>
      <div class="detail detail-time">
        <svg width="30" height="30" viewBox="0 0 30 30"><circle cx="15" cy="15" r="15" fill="#f39219"/><circle cx="15" cy="15" r="7" fill="none" stroke="#fff" stroke-width="1.6"/><path d="M15 11v4l3 2" fill="none" stroke="#fff" stroke-width="1.6"/></svg>
        <p>11:00AM<br>to 7:00PM</p>
      </div>
      <div class="vrule vrule-2"></div>
      <div class="detail detail-venue">
        <svg width="30" height="30" viewBox="0 0 30 30"><circle cx="15" cy="15" r="15" fill="#f39219"/><path d="M15 23s-6-6-6-10a6 6 0 0 1 12 0c0 4-6 10-6 10z" fill="none" stroke="#fff" stroke-width="1.6"/><circle cx="15" cy="13" r="2" fill="none" stroke="#fff" stroke-width="1.4"/></svg>
        <p>Belmora Hotel,<br>4875 Wexley Avenue,<br>Portland, Maine 04102<br>(Room: Juniper)</p>
      </div>
    </div>
    <div class="footer-rule"></div>
    <div class="footer-brand">
      <span class="brand-dot"></span>
      <span class="brand-name">TOLVEX</span>
    </div>
    <div class="contacts">
      <div class="contact">
        <svg width="24" height="24" viewBox="0 0 24 24" fill="none" stroke="#fff" stroke-width="1.5"><circle cx="12" cy="12" r="10"/><ellipse cx="12" cy="12" rx="4.5" ry="10"/><line x1="2" y1="12" x2="22" y2="12"/></svg>
        <span>tolvex.org</span>
        <svg width="30" height="24" viewBox="0 0 30 24" fill="none" stroke="#fff" stroke-width="1.5"><path d="M3 9c0-4 24-4 24 0v2h-6V8H9v3H3z"/><path d="M8 12l-3 9h20l-3-9z"/><circle cx="15" cy="16" r="2.5"/></svg>
        <span>207 555 3184</span>
      </div>
      <div class="contact">
        <svg width="24" height="20" viewBox="0 0 24 20" fill="none" stroke="#fff" stroke-width="1.5"><rect x="1" y="2" width="22" height="16"/><path d="M1 2l11 9 11-9"/></svg>
        <span>contact@brookhavenfold.org</span>
      </div>
    </div>
  </div>
</div>
</body>
</html>
```